Web Design Project - Shipping Industry

Goals and Objectives
The objective of the new website is to create a more modern look and feel. The site will also allow for a more effective means of communicating with members while providing the public with information and developments in the local, regional and international shipping industry.
Scope
The website will highlight the history of the organisation inclusive of text and photographs. It will take visitors through the years from beginning to present. Information on the history of the shipping industry will also be included.
It will feature current articles on the organisation, its members and stakeholders in the shipping industry. Member information as well as pertinent details regarding the organisation’s subsidiaries will be documented for the website.
Information as it relates to shipping statistics, case studies, laws and regulations, international treaties and trade documents, shipping terms, careers in shipping, job opportunities, training opportunities, information for shippers including port listing and trade lanes will be main features of the content for the website.
The Association’s community involvement, industry calendar events and related links relevant industry members will also be featured.
Target Market
• The General Public;
• Members of the organization;
• Shipping Industry Stakeholders (local, regional and international);
• Tertiary students conducting research.
• Potential employees
• Potential Business Partners
Best Practice Bench Marketing
The following websites are being looked at:
• Korvel Quayworks - http://www.korvelquayworks.example/ (preferred look)
• Tessaly Maritime Association - http://www.tma-freight.example/ (like image transition on main page)
• Drovna - http://www.drovna.example (professional look)
• PLW - http://www.pelworth.example (preferred color: blue in logo)
• Quillo - http://www.quillo.example/electronics/tv-video-audio/ (preferred look for links page: image + short text below + visit site link)
Expected Result
• 3 - 5 pages which must include: [1] main page [2] standard page [3] links page

```html
<!DOCTYPE html>
<html lang="en">
<head>
<meta charset="utf-8">
<title>The Harbourline Shipping Association</title>
<link rel="stylesheet" href="https://fonts.googleapis.com/css2?family=Arimo:wght@400;700&family=Tinos&family=Varela+Round&display=swap">
<style>
:root{
  --bg-deep:#0b3ea8;
  --bg-mid:#1a5fd0;
  --brand:#1a7fd8;
  --navy:#1e3c94;
  --green:#4f9a3a;
  --panel:#eef5fd;
  --panel-line:#9cc4ea;
  --discover:#d9e9fb;
  --text:#333;
  --muted:#555;
  --white:#fff;
  --footer:#0d3aa0;
}
*{margin:0;padding:0;box-sizing:border-box}
html,body{width:1200px;height:899px;overflow:hidden}
body{
  background:radial-gradient(ellipse at 50% 40%,var(--bg-mid) 0%,var(--bg-deep) 70%);
  font-family:Arimo,Arial,sans-serif;color:var(--text);position:relative;
}
.page{position:absolute;left:195px;top:0;width:805px;height:842px;background:var(--white)}
.abs{position:absolute}
h1,h2,h3{font-weight:normal}
.brand-mark{left:133px;top:26px;width:46px;height:46px;border-radius:50%;background:var(--brand)}
.brand-name{left:36px;top:79px;font-family:Tinos,serif;font-size:16px;color:var(--brand);white-space:nowrap}
.btn{top:0;height:22px;width:77px;color:#fff;font-size:11px;text-align:center;line-height:22px;border-radius:0 0 5px 5px;font-family:"Varela Round",sans-serif}
.btn-register{left:602px;background:linear-gradient(#5aa04a,#2f7428)}
.btn-login{left:685px;background:linear-gradient(#3a8cf0,#1458c8)}
.search{left:593px;top:42px;width:190px;height:24px;border:1px solid #d6dbe2;border-radius:12px 4px 4px 12px;background:linear-gradient(#f0f2f5,#fff)}
.search span{position:absolute;left:18px;top:7px;font-size:9px;font-style:italic;color:#999}
.search-btn{position:absolute;right:-1px;top:-1px;width:28px;height:24px;background:#1a6fdc;border-radius:0 4px 4px 0}
.nav{top:92px;height:28px;background:linear-gradient(#3d92f2,#1458c8);color:#fff;font-size:9.5px;text-align:center;line-height:30px;border-radius:3px 3px 0 0}
.nav-home{left:308px;top:92px;font-size:9.5px;line-height:30px;color:#eef3fa}
.hero{left:24px;top:120px;width:757px;height:235px;background:var(--panel);border:1px solid var(--panel-line);border-radius:3px}
.hero-title{left:48px;top:133px;width:210px;font-size:13px;font-weight:700;color:var(--brand);line-height:16px}
.hero-text{left:48px;top:177px;width:202px;font-size:10.3px;line-height:15.4px;color:var(--muted)}
.hero-photo{left:280px;top:132px;width:484px;height:206px;background:linear-gradient(180deg,#8a949c 0%,#7d8588 14%,#8e5a4e 24%,#a84a3e 34%,#5a7080 44%,#2f5f82 60%,#245273 100%)}
.pager{top:307px;width:19px;height:19px;background:#222;border:1px solid #888;color:#fff;font-size:10px;text-align:center;line-height:17px}
.pager.on{background:var(--brand);border-color:var(--brand)}
.h2{font-family:"Varela Round",sans-serif;color:var(--navy);font-size:15px;white-space:nowrap}
.news-thumb{left:27px;width:72px;height:47px;border:1px solid #ccc}
.t-ship{background:linear-gradient(180deg,#7f9ab0 0%,#b04a3a 45%,#2d5f8a 70%,#1f4a70 100%)}
.t-workers{background:linear-gradient(135deg,#c9a14a 0%,#5a86b0 45%,#2f6a9c 100%)}
.t-cranes{background:linear-gradient(180deg,#b8c6d4 0%,#5d7996 50%,#8a4a4a 75%,#3a5a7a 100%)}
.news-title{left:113px;font-family:"Varela Round",sans-serif;font-size:13px;color:var(--green);white-space:nowrap}
.news-title small{font-family:Arimo,sans-serif;font-size:9.5px;color:#555;margin-left:5px}
.news-body{left:114px;width:234px;font-size:10.3px;line-height:15.4px;color:#222}
.news-body a,.discover-text a{color:var(--brand);text-decoration:underline}
.rule{left:27px;width:326px;border-top:1px dashed #bbb}
.svc-photo{left:27px;top:719px;width:170px;height:70px;border:1px solid #9b4a8c;background:linear-gradient(160deg,#8a98a8 0%,#5a7690 35%,#2f587c 60%,#9a6a5a 100%)}
.svc-label{left:28px;top:720px;width:168px;height:11px;background:rgba(20,40,90,.85);color:#fff;font-size:8.5px;font-weight:700;padding-left:2px;line-height:11px}
.svc-caption{left:48px;top:802px;font-size:10.3px;color:#444}
.social{top:735px;width:37px;height:37px;border-radius:50%;background:#fff;border:1px solid #ddd;box-shadow:0 1px 2px rgba(0,0,0,.15)}
.discover{left:371px;top:382px;width:410px;height:191px;background:var(--discover);border:1px solid var(--panel-line);border-radius:8px}
.discover-text{left:396px;top:421px;width:140px;font-size:10.3px;line-height:15.4px;color:#333}
.video{left:547px;top:421px;width:220px;height:123px;background:linear-gradient(160deg,#5a6b80 0%,#9a4a3a 30%,#4f7490 60%,#c4c8cc 100%)}
.gal{top:624px;width:74px;height:49px}
.g1{background:linear-gradient(180deg,#6c9ad0 0%,#d8853a 45%,#7a6a5a 100%)}
.g2{background:linear-gradient(180deg,#7fa0c0 0%,#c05a4a 40%,#4a8a6a 65%,#3a6a9a 100%)}
.g3{background:linear-gradient(90deg,#d8a030 0%,#6a4a3a 30%,#c8a070 60%,#d8a030 100%)}
.g4{background:linear-gradient(180deg,#d8dde2 0%,#b83a3a 30%,#3a8080 60%,#2a5a5a 100%)}
.arrow{font-size:9px;color:#555}
.links-band{left:376px;top:731px;width:400px;height:75px;background:linear-gradient(90deg,#e4e4e4,#fafafa 20%,#fafafa 80%,#e4e4e4)}
.badge{top:751px;width:38px;height:34px;background:#1a5fb8;border-radius:4px}
.badge.round{border-radius:50%;background:#2a5da8}
.footer{position:absolute;left:195px;top:842px;width:805px;height:57px;background:var(--footer)}
.foot-copy{left:3px;top:25px;font-size:9.5px;color:#fff}
.foot-mark{left:503px;top:16px;width:24px;height:24px;border-radius:50%;background:#fff}
.foot-name{left:540px;top:18px;font-family:Tinos,serif;font-size:16px;color:#fff;white-space:nowrap}
</style>
</head>
<body>
<div class="page">
  <header>
    <div class="abs brand-mark"></div>
    <div class="abs brand-name">the harbourline shipping association</div>
    <a class="abs btn btn-register">REGISTER</a>
    <a class="abs btn btn-login">LOGIN</a>
    <div class="abs search"><span>Search</span>
      <div class="search-btn"><svg width="28" height="24" viewBox="0 0 28 24"><circle cx="13" cy="11" r="4" fill="none" stroke="#fff" stroke-width="1.8"/><line x1="16" y1="14" x2="19" y2="17" stroke="#fff" stroke-width="2"/></svg></div>
    </div>
    <nav>
      <span class="abs nav-home">HOME</span>
      <a class="abs nav" style="left:350px;width:77px">ABOUT US</a>
      <a class="abs nav" style="left:434px;width:77px">SERVICES</a>
      <a class="abs nav" style="left:517px;width:77px">NEWS</a>
      <a class="abs nav" style="left:601px;width:77px">CUSTOMERS</a>
      <a class="abs nav" style="left:685px;width:77px">CONTACT</a>
    </nav>
  </header>

  <section>
    <div class="abs hero"></div>
    <h1 class="abs hero-title">Lorem ipsum dolor sit amet consectetur</h1>
    <p class="abs hero-text">Nulla ipsum nibh, dignissim ut mattis at, ornare vel mi. Aliquam pretium tincidunt sagittis. Cum sociis natoque penatibus et magnis dis parturient montes, nascetur ridiculus mus. Etiam quis nisi vitae metus dictum dignissim. Donec a turpis enim, ut sollicitudin nisl. Aenean felis est, vestibulum fermentum pellentesque vitae, fermentum a eros. Praesent eget velit dui.</p>
    <div class="abs hero-photo" role="img" aria-label="Container ship sailing past a busy port with stacked containers"></div>
    <span class="abs pager on" style="left:632px">1</span>
    <span class="abs pager" style="left:656px">2</span>
    <span class="abs pager" style="left:680px">3</span>
    <span class="abs pager" style="left:706px">4</span>
    <span class="abs pager" style="left:731px">5</span>
  </section>

  <section>
    <h2 class="abs h2" style="left:27px;top:376px">LATEST NEWS</h2>

    <div class="abs news-thumb t-ship" style="top:406px" role="img" aria-label="Container ship at sea"></div>
    <h3 class="abs news-title" style="top:401px">Lorem ipsum dolor sit amet<small>19th May 2012</small></h3>
    <p class="abs news-body" style="top:421px">Nnummy nibh euismod tincidunt ut laoreet dolore magna aliquam erat volutpat. Ut wisi enim ad minim veniam, quis nostrud exerci. &nbsp;<a>View All </a></p>
    <div class="abs rule" style="top:482px"></div>

    <div class="abs news-thumb t-workers" style="top:500px" role="img" aria-label="Dock workers in hard hats"></div>
    <h3 class="abs news-title" style="top:494px">Lorem ipsum dolor sit amet<small>19th May 2012</small></h3>
    <p class="abs news-body" style="top:514px">Nnummy nibh euismod tincidunt ut laoreet dolore magna aliquam erat volutpat. Ut wisi enim ad minim veniam, quis nostrud exerci. &nbsp;<a>View All </a></p>
    <div class="abs rule" style="top:576px"></div>

    <div class="abs news-thumb t-cranes" style="top:597px" role="img" aria-label="Cranes loading a cargo ship"></div>
    <h3 class="abs news-title" style="top:592px">Lorem ipsum dolor sit amet<small>19th May 2012</small></h3>
    <p class="abs news-body" style="top:612px">Nnummy nibh euismod tincidunt ut laoreet dolore magna aliquam erat volutpat. Ut wisi enim ad minim veniam, quis nostrud exerci &nbsp;<a>View All </a></p>
    <div class="abs rule" style="top:674px"></div>
  </section>

  <section>
    <h2 class="abs h2" style="left:27px;top:689px">SERVICES</h2>
    <div class="abs svc-photo" role="img" aria-label="Aerial view of the harbour and terminals"></div>
    <div class="abs svc-label">The Port of Calder Bay</div>
    <p class="abs svc-caption">Lorem ipsum dolor sit amet</p>
    <a class="abs social" style="left:223px" aria-label="Photo sharing"></a>
    <a class="abs social" style="left:269px" aria-label="News feed"></a>
  </section>

  <section>
    <div class="abs discover"></div>
    <h2 class="abs h2" style="left:390px;top:395px;font-size:13px">DISCOVER THE PORT OF CALDER BAY</h2>
    <p class="abs discover-text">Registered as a Trade Union, one of the primary functions of the Association is the manangement of certain categories of labour on the Port. In addition, the Association acts on behalf of its members .. <a>Read More</a></p>
    <div class="abs video" role="img" aria-label="Video of container cranes and stacks at the port"></div>
    <svg class="abs" style="left:547px;top:421px" width="220" height="123" viewBox="0 0 220 123">
      <circle cx="114" cy="65" r="24" fill="rgba(0,0,0,.25)" stroke="#fff" stroke-width="2.5"/>
      <path d="M107 52 L127 65 L107 78 Z" fill="#fff"/>
      <rect x="0" y="113" width="220" height="10" fill="rgba(0,0,0,.6)"/>
      <path d="M6 115 L11 118 L6 121 Z" fill="#fff"/>
      <rect x="18" y="117" width="190" height="2" fill="#888"/>
    </svg>
  </section>

  <section>
    <h2 class="abs h2" style="left:388px;top:593px;font-size:13.5px">GALLERY</h2>
    <span class="abs arrow" style="left:377px;top:641px">&#9664;</span>
    <div class="abs gal g1" style="left:397px" role="img" aria-label="Container lifted by a crane"></div>
    <div class="abs gal g2" style="left:490px" role="img" aria-label="Deck of a fully loaded container ship"></div>
    <div class="abs gal g3" style="left:584px" role="img" aria-label="Warehouse with stacked boxes"></div>
    <div class="abs gal g4" style="left:676px" role="img" aria-label="Bow of a ship beside port cranes"></div>
    <span class="abs arrow" style="left:763px;top:641px">&#9654;</span>
  </section>

  <section>
    <h2 class="abs h2" style="left:388px;top:697px;font-size:13.5px">LINKS</h2>
    <div class="abs links-band"></div>
    <svg class="abs" style="left:392px;top:758px" width="14" height="22" viewBox="0 0 14 22"><path d="M11 2 L3 11 L11 20" fill="none" stroke="#aaa" stroke-width="3"/></svg>
    <div class="abs badge" style="left:439px" aria-label="Partner"></div>
    <div class="abs badge" style="left:507px;background:#5aa04a" aria-label="Partner"></div>
    <div class="abs badge round" style="left:572px" aria-label="Partner"></div>
    <div class="abs badge round" style="left:631px;background:#8aa0c8" aria-label="Partner"></div>
    <div class="abs badge" style="left:692px;background:#e0a020" aria-label="Partner"></div>
    <svg class="abs" style="left:750px;top:758px" width="14" height="22" viewBox="0 0 14 22"><path d="M3 2 L11 11 L3 20" fill="none" stroke="#aaa" stroke-width="3"/></svg>
  </section>
</div>

<footer class="footer">
  <p class="abs foot-copy">© The Harbourline Shipping Association 2012, All Right Reserved</p>
  <div class="abs foot-mark"></div>
  <div class="abs foot-name">The Harbourline Shipping Association</div>
</footer>
</body>
</html>
```